Business Card Design Project

Actor, Producer, Vocal Coach, Choral Director, Song WriterPhone: (215) 555-0142 Fax: (215) 856-3933Email: waltierblocker@gmail.comFacebook: facebook.com/waltier.blockerTwitter: @thedf482

Industry/Entity Type

Business

Contact Information for Business Card

Business Cards that include my picture

Colors

Designer to choose colors to be used in the design.

```html
<!DOCTYPE html>
<html lang="en">
<head>
<meta charset="utf-8">
<title>Dorian Fellsmore – Business Card</title>
<link rel="stylesheet" href="https://fonts.googleapis.com/css2?family=Cinzel:wght@500&family=PT+Sans:wght@400&display=swap">
<style>
  :root {
    --page-bg: #e4e2e0;
    --card-top: #f7f6f5;
    --card-bottom: #ecebea;
    --band: #2a2a2a;
    --ink: #1c1c1c;
    --photo-skin: #7a5646;
    --photo-mid: #c9b7ae;
    --photo-shirt: #f3f2f1;
    --photo-base: #e6e3e1;
  }
  * { margin: 0; padding: 0; box-sizing: border-box; }
  html, body {
    width: 1200px; height: 900px; overflow: hidden;
    background: var(--page-bg);
  }
  .business-card {
    position: absolute;
    left: 100px; top: 140px;
    width: 1000px; height: 620px;
    background: linear-gradient(180deg, var(--card-top) 0%, var(--card-bottom) 100%);
    box-shadow: 0 10px 30px rgba(0,0,0,0.15);
    overflow: hidden;
  }
  .portrait {
    position: absolute;
    left: 55px; top: 110px;
    width: 440px; height: 414px;
    border-radius: 6px 6px 0 0;
    background: linear-gradient(180deg,
      var(--photo-skin) 0%,
      var(--photo-mid) 32%,
      var(--photo-shirt) 55%,
      var(--photo-base) 100%);
  }
  .footer-band {
    position: absolute;
    left: 0; bottom: 0;
    width: 100%; height: 96px;
    background: var(--band);
  }
  .details {
    position: absolute;
    left: 561px; top: 168px;
    color: var(--ink);
    font-family: "PT Sans", sans-serif;
  }
  .name {
    font-family: "Cinzel", serif;
    font-weight: 500;
    font-size: 35px;
    letter-spacing: 0.5px;
    line-height: 1;
  }
  .roles {
    margin-top: 12px;
    font-size: 26px;
    line-height: 36px;
  }
  .contact-list, .social-list {
    list-style: none;
    font-size: 26px;
  }
  .contact-list { margin-top: 14px; }
  .contact-list li { height: 36px; display: flex; align-items: center; }
  .social-list { margin-top: 22px; }
  .social-list li { height: 41px; display: flex; align-items: center; }
  .icon { width: 20px; height: 20px; margin-right: 12px; flex: none; fill: var(--ink); }
  .social-mark {
    width: 22px; height: 22px; margin-right: 10px; flex: none;
    border-radius: 3px;
    background: var(--ink);
  }
</style>
</head>
<body>
  <article class="business-card">
    <div class="portrait" role="img" aria-label="Portrait photo of Dorian Fellsmore in a white shirt and pink tie"></div>

    <section class="details">
      <h1 class="name">DORIAN FELLSMORE</h1>
      <p class="roles">Actor, Producer, Vocal Coach,<br>Choral Director, Song Writer</p>

      <ul class="contact-list">
        <li>
          <svg class="icon" viewBox="0 0 20 20" aria-hidden="true"><path d="M4 1l4 4-2.2 2.6c1.3 2.7 3.3 4.7 6 6L14.4 11.4l4 4L16 18.5C8.5 18 2 11.5 1.5 4z"/></svg>
          (215) 555-0142
        </li>
        <li>
          <svg class="icon" viewBox="0 0 20 20" aria-hidden="true"><rect x="1" y="6" width="4" height="13" rx="1"/><path d="M6 6h13v13H6zM8 1h9v5H8z"/><rect x="9" y="9" width="2" height="2" fill="#fff"/><rect x="13" y="9" width="2" height="2" fill="#fff"/><rect x="9" y="13" width="2" height="2" fill="#fff"/><rect x="13" y="13" width="2" height="2" fill="#fff"/></svg>
          (215) 555-0187
        </li>
        <li>
          <svg class="icon" viewBox="0 0 20 20" aria-hidden="true"><path d="M1 4h18v12H1z"/><path d="M1.5 4.5L10 11l8.5-6.5" fill="none" stroke="#fff" stroke-width="1.6"/></svg>
          dorianfellsmore@postlane.net
        </li>
      </ul>

      <ul class="social-list">
        <li><span class="social-mark" aria-hidden="true"></span>@thedf482</li>
        <li><span class="social-mark" aria-hidden="true"></span>@dorian.fellsmore</li>
      </ul>
    </section>

    <div class="footer-band"></div>
  </article>
</body>
</html>
```